Website redesign www.marigoldlawpc.com law firm site

Need to redesign the website that I currently have to look more modern and professional. Would also like to be able to make updates and post without having a huge hassle. See current www.marigoldlawpc.com. I just think that it looks very immature and it's very templated there's no ability for me to make posts or Add links or anything like that

Target Market(s)

California people looking for a powerhouse attorney in

Industry/Entity Type

Legal

Number of Pages Required

3 page

Font styles to use
Serif
Sans Serif

Colors
ec1f27
000000
ffffff

Requirements
Must have
• Must be mobile friendly. Must look professional and have ability to post links to other websites. Must have ability to post blogs or articles. Would like to be able to read my FeeTrove account and also have the ability to upload forms for people to download
Nice to have
• Simple design easy to use and not cluttered with too much text

```html
<!DOCTYPE html>
<html lang="en">
<head>
<meta charset="utf-8">
<title>Marigold Law PC</title>
<link href="https://fonts.googleapis.com/css2?family=Cinzel:wght@400;700&family=Josefin+Sans:wght@400;600;700&family=Open+Sans:wght@400;600&display=swap" rel="stylesheet">
<style>
:root{
  --red:#ec1f27;
  --black:#000;
  --white:#fff;
  --ink:#222;
  --text:#555;
  --muted:#8a8a8a;
  --line:#d8d8d8;
  --grey-btn:#d4d4d4;
  --band:#f0f0f0;
  --footer:#1c1c1c;
}
*{box-sizing:border-box;margin:0;padding:0}
html,body{width:1200px;height:2687px;overflow:hidden}
body{position:relative;background:var(--white);font-family:"Open Sans",Arial,sans-serif;color:var(--text)}

/* header */
.site-header{position:absolute;left:0;top:0;width:1200px;height:80px;background:var(--white)}
.brand{position:absolute;left:163px;top:27px;font-family:"Josefin Sans",Arial,sans-serif;font-weight:600;font-size:24px;color:var(--ink);line-height:28px;white-space:nowrap}
.contact-top{position:absolute;left:715px;top:22px;font-size:13px;line-height:17px;color:var(--ink)}
.contact-top .mail{color:var(--muted);font-size:12px}
.contact-top svg{position:absolute;left:-25px;top:3px}
.social{position:absolute;top:25px;display:flex;gap:9px}
.social span{width:27px;height:27px;display:block;border-radius:3px}

.main-nav{position:absolute;left:0;top:80px;width:1200px;height:35px;background:linear-gradient(#2a2a2a,#050505)}
.main-nav ul{list-style:none;display:flex;position:absolute;left:158px;top:0;height:35px}
.main-nav li{font-family:"Cinzel",Georgia,serif;font-size:12px;color:var(--white);height:35px;line-height:36px;padding:0 34px;position:relative;white-space:nowrap}
.main-nav li+li::before{content:"";position:absolute;left:0;top:12px;height:12px;border-left:1px solid #666}
.main-nav li.active{background:var(--red);padding:0 36px}

/* hero */
.hero{position:absolute;left:0;top:115px;width:1200px;height:458px;background:linear-gradient(100deg,#b9bcc1 0%,#d8d2cb 35%,#c8b8a8 60%,#e6e4e2 100%)}
.hero-caption{position:absolute;left:165px;top:157px;width:329px;height:77px;background:rgba(30,30,30,.82);padding:9px 8px;color:var(--white)}
.hero-caption .kicker{font-family:"Cinzel",Georgia,serif;font-size:17px;letter-spacing:1px;line-height:22px}
.hero-caption .title{font-family:"Cinzel",Georgia,serif;font-size:32px;line-height:38px;white-space:nowrap}
.btn-red{position:absolute;background:var(--red);color:var(--white);font-family:"Cinzel",Georgia,serif;font-size:12px;font-weight:700;white-space:nowrap}
.hero .more{left:161px;top:247px;width:117px;height:29px;line-height:29px;padding-left:14px}
.slide-arrow{position:absolute;top:184px;width:22px;height:80px;background:rgba(255,255,255,.55)}
.thumbs{position:absolute;left:520px;top:433px;display:flex;gap:4px}
.thumbs span{width:50px;height:39px;border:3px solid var(--white);background:#9a9ea6;display:block}

/* section heads */
.sec-title{position:absolute;font-family:"Josefin Sans",Arial,sans-serif;font-weight:700;font-size:29px;color:var(--ink);white-space:nowrap}
.sec-title em{font-style:normal;color:var(--red)}
.sec-title svg{vertical-align:-4px;margin-right:8px}
.rule{position:absolute;height:1px;background:var(--line)}

/* welcome */
.welcome-copy{position:absolute;left:161px;top:667px;width:675px;font-size:12.5px;line-height:22px;color:#444}
.welcome-copy p+p{margin-top:9px}
.btn-grey{position:absolute;background:var(--grey-btn);color:#444;font-family:"Josefin Sans",Arial,sans-serif;font-weight:600;font-size:14px;padding-left:15px;white-space:nowrap}
.profile{position:absolute;left:874px;top:620px;width:165px;height:189px;background:var(--red)}
.profile .photo{position:absolute;left:5px;top:5px;width:155px;height:150px;background:linear-gradient(#4a3a30,#7a6455)}
.profile .name{position:absolute;left:0;bottom:6px;width:100%;text-align:center;color:var(--white);font-family:"Josefin Sans",Arial,sans-serif;font-weight:700;font-size:15px}

/* practice */
.practice{position:absolute;left:0;top:908px;width:1200px;height:695px;background:linear-gradient(#2b2520,#151211 55%,#0c0b0b)}
.practice .sec-title{color:var(--white)}
.area{position:absolute;width:276px}
.area .pic{height:171px;border:3px solid #e6e6e6}
.area .label{height:41px;line-height:43px;text-align:center;color:var(--white);font-family:"Josefin Sans",Arial,sans-serif;font-size:15px;font-weight:600}
.area .label svg{vertical-align:-3px;margin-right:8px}
.area.active .label{background:var(--red)}
.practice .view-all{left:487px;top:618px;width:226px;height:37px;line-height:39px;text-align:center;font-family:"Josefin Sans",Arial,sans-serif;font-size:14px;font-weight:600}

/* account / inquiry */
.account-copy{position:absolute;left:161px;top:1697px;width:410px;font-size:12.5px;line-height:22.5px;color:#444}
.field{position:absolute;left:631px;width:408px;height:32px;border:1px solid #dcdcdc;font-size:10.5px;color:#999;padding:9px 14px}
.field svg{position:absolute;right:12px;top:12px}

/* blog */
.blog{position:absolute;left:0;top:1967px;width:1200px;height:433px;background:var(--band)}
.post{position:absolute;top:105px;width:263px;height:283px;background:var(--white)}
.post .pic{height:152px}
.post .date{position:absolute;left:112px;top:126px;width:42px;height:46px;background:var(--red);color:var(--white);text-align:center;font-family:"Josefin Sans",Arial,sans-serif;font-size:14px;line-height:17px;padding-top:6px}
.post .date b{display:block;font-size:20px;font-weight:400}
.post .meta{position:absolute;top:158px;left:12px;right:12px;font-size:8.5px;color:#888;display:flex;gap:10px}
.post .meta .who{margin-right:auto}
.post h3{position:absolute;top:178px;left:12px;font-family:"Josefin Sans",Arial,sans-serif;font-weight:400;font-size:15px;color:#333;white-space:nowrap}
.post p{position:absolute;top:208px;left:12px;right:16px;font-size:12.5px;line-height:21px;color:#888}

/* footer */
.site-footer{position:absolute;left:0;top:2400px;width:1200px;height:247px;background:var(--footer);color:#aaa}
.site-footer h4{position:absolute;top:40px;color:var(--white);font-family:"Josefin Sans",Arial,sans-serif;font-size:16px;font-weight:600}
.quick{position:absolute;left:163px;top:67px;list-style:none;font-size:11px;line-height:23.5px}
.quick li::before{content:"›";margin-right:8px}
.newsletter{position:absolute;left:347px;top:67px;width:180px;font-size:10.5px;line-height:17px}
.news-input{position:absolute;left:347px;top:106px;width:184px;height:32px;background:#444;color:#ddd;font-size:10.5px;padding:9px 12px}
.site-footer .subscribe{left:347px;top:148px;width:113px;height:33px;line-height:35px;padding-left:13px;font-family:"Josefin Sans",Arial,sans-serif;font-size:14px;font-weight:600}
.address{position:absolute;left:582px;top:68px;font-size:11px;line-height:23px}
.map{position:absolute;left:788px;top:40px;width:250px;height:138px;background:linear-gradient(135deg,#e9e5d6,#cfe0c3 55%,#b8d3e8)}
.map-link{position:absolute;left:788px;top:184px;font-size:11px;text-decoration:underline}
.copyright{position:absolute;left:0;top:2647px;width:1200px;height:40px;background:var(--red);color:var(--white);text-align:center;line-height:40px;font-size:11px}
</style>
</head>
<body>

<header class="site-header">
  <div class="brand">Marigold Law PC</div>
  <div class="contact-top">
    <svg width="14" height="22" viewBox="0 0 14 22"><rect x="1" y="1" width="12" height="20" rx="2" fill="none" stroke="#888" stroke-width="2"/><rect x="5" y="16" width="4" height="2" fill="#888"/></svg>
    (530) 555-0142<br><span class="mail">elena@marigoldlawgroup.com</span>
  </div>
  <div class="social" style="left:939px">
    <span style="background:#3b5998"></span><span style="background:#0e76a8"></span><span style="background:#1fa4d8"></span>
  </div>
</header>

<nav class="main-nav">
  <ul>
    <li class="active">Home</li><li>Attorney Profile</li><li>Practice Areas</li><li>Client Reviews</li><li>Links</li><li>Contact Us</li>
  </ul>
</nav>

<section class="hero" role="img" aria-label="Photo of an attorney reviewing a tablet with a smiling couple">
  <div class="slide-arrow" style="left:0"></div>
  <div class="slide-arrow" style="right:0"></div>
  <div class="hero-caption">
    <div class="kicker">The Greatest Firm</div>
    <div class="title">You Can Trust</div>
  </div>
  <div class="btn-red more">MORE INFO &#8250;</div>
  <div class="thumbs"><span></span><span></span><span></span></div>
</section>

<section class="welcome">
  <h2 class="sec-title" style="left:161px;top:611px"><svg width="32" height="28" viewBox="0 0 32 28"><rect x="6" y="3" width="14" height="7" transform="rotate(-35 13 6)" fill="#999"/><rect x="13" y="9" width="4" height="16" transform="rotate(-35 15 17)" fill="#999"/><rect x="2" y="24" width="14" height="3" fill="#999"/></svg>WELCOME TO <em>MARIGOLDLAWPC</em></h2>
  <div class="rule" style="left:204px;top:652px;width:630px"></div>
  <div class="welcome-copy">
    <p>Find the big firm style legal counsel you can work with in your hometown region at Marigold Law P.C., in Chico, CA. Attorney Elena M. Reyes, Esq., offers a boutique law firm opportunity for clients who want to enjoy all the advantages of her broad legal experience and education.</p>
    <p>She works closely with clients, and has the knowledge of many areas of law to apply to your situation. This is very helpful when it is necessary to incorporate those different areas of law practice into creating a winning argument for your unique case.</p>
  </div>
  <div class="btn-grey" style="left:161px;top:825px;width:128px;height:36px;line-height:38px">READ MORE &#8250;</div>
  <figure class="profile">
    <div class="photo" role="img" aria-label="Portrait of attorney Elena M. Reyes"></div>
    <figcaption class="name">Elena M. Reyes</figcaption>
  </figure>
</section>

<section class="practice">
  <h2 class="sec-title" style="left:455px;top:34px"><svg width="32" height="28" viewBox="0 0 32 28"><rect x="6" y="3" width="14" height="7" transform="rotate(-35 13 6)" fill="#ddd"/><rect x="13" y="9" width="4" height="16" transform="rotate(-35 15 17)" fill="#ddd"/><rect x="2" y="24" width="14" height="3" fill="#ddd"/></svg>PRACTICE <em>AREAS</em></h2>

  <div class="area active" style="left:161px;top:125px">
    <div class="pic" role="img" aria-label="Businessman signing a contract beside a justice statue" style="background:linear-gradient(135deg,#e8e8e8,#9a9a9a)"></div>
    <div class="label"><svg width="18" height="16"><rect x="8" y="1" width="2" height="14" fill="#fff"/><rect x="2" y="3" width="14" height="2" fill="#fff"/><rect x="4" y="14" width="10" height="2" fill="#fff"/></svg>BUSINESS LAW</div>
  </div>
  <div class="area" style="left:462px;top:125px">
    <div class="pic" role="img" aria-label="Hand signing papers beside a model house" style="background:linear-gradient(135deg,#f0eee8,#a9a7a2)"></div>
    <div class="label"><svg width="18" height="16"><path d="M9 1 L17 8 H14 V15 H4 V8 H1 Z" fill="#ec1f27"/></svg>REAL ESTATE LAW</div>
  </div>
  <div class="area" style="left:761px;top:125px">
    <div class="pic" role="img" aria-label="Gavel resting on a bankruptcy petition" style="background:linear-gradient(135deg,#c87a3c,#f2ece2 60%)"></div>
    <div class="label"><svg width="16" height="16"><circle cx="8" cy="4" r="3" fill="#ec1f27"/><rect x="3" y="8" width="10" height="8" fill="#ec1f27"/></svg>BANKRUPTCY</div>
  </div>
  <div class="area" style="left:161px;top:373px">
    <div class="pic" role="img" aria-label="Cupped hands holding a paper family cut-out" style="background:linear-gradient(135deg,#e7b99a,#8c5e46)"></div>
    <div class="label"><svg width="20" height="14"><rect x="1" y="4" width="5" height="10" fill="#ec1f27"/><rect x="8" y="6" width="4" height="8" fill="#ec1f27"/><rect x="14" y="4" width="5" height="10" fill="#ec1f27"/></svg>FAMILY LAW</div>
  </div>
  <div class="area" style="left:462px;top:373px">
    <div class="pic" role="img" aria-label="Handcuffed hands resting on a courtroom table" style="background:linear-gradient(#2a2a2a,#7a4a28)"></div>
    <div class="label"><svg width="16" height="16"><circle cx="8" cy="8" r="6" fill="none" stroke="#ec1f27" stroke-width="2"/></svg>CRIMINAL LAW</div>
  </div>
  <div class="area" style="left:761px;top:373px">
    <div class="pic" role="img" aria-label="Gavel in front of shelves of law books" style="background:linear-gradient(#a9864a,#3a1e12)"></div>
    <div class="label"><svg width="12" height="16"><rect x="1" y="1" width="10" height="15" fill="#ec1f27"/></svg>CIVIL LITIGATION</div>
  </div>

  <div class="btn-red view-all">VIEW ALL PRACTICE AREAS &#8250;</div>
</section>

<section class="account">
  <h2 class="sec-title" style="left:161px;top:1641px"><svg width="32" height="28" viewBox="0 0 32 28"><rect x="6" y="3" width="14" height="7" transform="rotate(-35 13 6)" fill="#999"/><rect x="13" y="9" width="4" height="16" transform="rotate(-35 15 17)" fill="#999"/><rect x="2" y="24" width="14" height="3" fill="#999"/></svg>FEETROVE <em>ACCOUNT</em></h2>
  <div class="rule" style="left:204px;top:1682px;width:364px"></div>
  <p class="account-copy">Ut wisi enim ad minim veniam, quis nostrud exerci tation ullamcorper suscipit lobortis nisl ut aliquip ex ea commodo consequat. Duis autem vel eum iriure dolor in hendrerit in vulputate velit esse molestie conse quat, vel illum dolore eu feugiat nulla facilisis at vero eros et accum san et iusto odio dignissim qui blandit praesent luptatum zzril delenit augue duis dolore te feugait nulla facilisi.Lorem ipsum dolor sit amet, consectetuer adipiscing elit, sed diam nonummy nibh…</p>
  <div class="btn-grey" style="left:161px;top:1889px;width:123px;height:36px;line-height:38px">READ MORE &#8250;</div>
</section>

<section class="inquiry">
  <h2 class="sec-title" style="left:628px;top:1641px"><svg width="32" height="28" viewBox="0 0 32 28"><rect x="6" y="3" width="14" height="7" transform="rotate(-35 13 6)" fill="#999"/><rect x="13" y="9" width="4" height="16" transform="rotate(-35 15 17)" fill="#999"/><rect x="2" y="24" width="14" height="3" fill="#999"/></svg>QUICK <em>INQUIRY</em></h2>
  <div class="rule" style="left:671px;top:1682px;width:368px"></div>
  <div class="field" style="top:1700px">Your Name</div>
  <div class="field" style="top:1746px">Subject<svg width="10" height="6"><path d="M1 1 L5 5 L9 1" fill="none" stroke="#999"/></svg></div>
  <div class="field" style="top:1792px">Your Email</div>
  <div class="field" style="top:1838px">Your Mobile No</div>
  <div class="btn-grey" style="left:631px;top:1889px;width:103px;height:36px;line-height:38px">SUBMIT &#8250;</div>
</section>

<section class="blog">
  <h2 class="sec-title" style="left:475px;top:37px"><svg width="32" height="28" viewBox="0 0 32 28"><rect x="6" y="3" width="14" height="7" transform="rotate(-35 13 6)" fill="#999"/><rect x="13" y="9" width="4" height="16" transform="rotate(-35 15 17)" fill="#999"/><rect x="2" y="24" width="14" height="3" fill="#999"/></svg>LATEST <em>BLOG</em></h2>

  <article class="post" style="left:161px">
    <div class="pic" role="img" aria-label="Businessman signing papers beside a model house" style="background:linear-gradient(135deg,#3a3f4a,#c9c3b8)"></div>
    <div class="date"><b>07</b>May</div>
    <div class="meta"><span class="who">Rina Dasgupta</span><span>111</span><span>160</span></div>
    <h3>Lorem ipsum dolor sit amet…</h3>
    <p>consectetuer adipiscing elit, sed diam nonummy nibh euismod tincidunt ut laoreet dolor er adipiscing elit,..[+]</p>
  </article>
  <article class="post" style="left:468px">
    <div class="pic" role="img" aria-label="Gavel on a criminal law document" style="background:linear-gradient(135deg,#7a4a2a,#e8e2d8)"></div>
    <div class="date"><b>07</b>May</div>
    <div class="meta"><span class="who">Rina Dasgupta</span><span>111</span><span>160</span></div>
    <h3>Lorem ipsum dolor sit amet…</h3>
    <p>consectetuer adipiscing elit, sed diam nonummy nibh euismod tincidunt ut laoreet dolor er adipiscing elit,..[+]</p>
  </article>
  <article class="post" style="left:776px">
    <div class="pic" role="img" aria-label="Hands sheltering a paper family cut-out" style="background:linear-gradient(135deg,#f2f2f2,#d8b8a2)"></div>
    <div class="date"><b>07</b>May</div>
    <div class="meta"><span class="who">Rina Dasgupta</span><span>111</span><span>160</span></div>
    <h3>Lorem ipsum dolor sit amet…</h3>
    <p>consectetuer adipiscing elit, sed diam nonummy nibh euismod tincidunt ut laoreet dolor er adipiscing elit,..[+]</p>
  </article>
</section>

<footer class="site-footer">
  <h4 style="left:163px">Quick Link</h4>
  <ul class="quick">
    <li>Home</li><li>About Us</li><li>Practice Areas</li><li>Attorneys</li><li>Blog</li><li>Links</li><li>Contact Us</li>
  </ul>
  <h4 style="left:347px">Join Our Newsletter</h4>
  <p class="newsletter">Subscribe to our Newsletter to get the latest scoop right to your inbox</p>
  <div class="news-input">Enter Your Email</div>
  <div class="btn-red subscribe">SUBSCRIBE &#8250;</div>
  <h4 style="left:582px">Contact Detail</h4>
  <div class="address">418 Oak Lane Suite 300<br>Chico, CA 95926<br>(530) 555-0142<br>elena@marigoldlawgroup.com</div>
  <div class="social" style="left:582px;top:167px;gap:8px">
    <span style="width:22px;height:22px;background:#3b5998"></span><span style="width:22px;height:22px;background:#1da1f2"></span><span style="width:22px;height:22px;background:#0e76a8"></span><span style="width:22px;height:22px;background:#1fa4d8"></span>
  </div>
  <div class="map" role="img" aria-label="Street map showing the Marigold Law PC office location"></div>
  <div class="map-link">View Map</div>
</footer>
<div class="copyright">Copyright &copy; 2016 Marigold Law Pc . All Right Reserved.</div>

</body>
</html>
```